Realtor branding business card

modern, simple and self branding. Broker office logo needs to be used but not emphasized. Looking to brand myself

Target Market(s)

buyers, sellers and investors

Industry/Entity Type

Realtor

Contact Information for Business Card

Sample of my current business card on file

Requirements
Must have
• my website - tobiasmerrowkl.com
• Realtor logo
• Fair housing logo
Nice to have
• Colors from office logo but not a must
Should not have
• Do not want headshot

```html
<!DOCTYPE html>
<html lang="en">
<head>
<meta charset="utf-8">
<title>Tobias Merrow – Realtor Business Card</title>
<link href="https://fonts.googleapis.com/css2?family=PT+Sans:wght@400;700&display=swap" rel="stylesheet">
<style>
  :root {
    --navy: #2a1d7c;
    --red: #dc2a22;
    --grey: #6f6f6f;
    --dark: #222222;
    --paper: #fbfbfb;
    --backdrop: #2b2b2b;
  }
  * { margin: 0; padding: 0; box-sizing: border-box; }
  html, body {
    width: 1200px; height: 892px; overflow: hidden;
    background: var(--backdrop);
    font-family: "PT Sans", Arial, sans-serif;
  }
  .sheet {
    position: relative; width: 1200px; height: 892px;
    display: flex; flex-direction: column; align-items: center; justify-content: center; gap: 32px;
  }
  .card {
    position: relative; width: 700px; height: 400px;
    background: var(--paper); overflow: hidden;
  }
  .brand-name {
    font-weight: 700; color: var(--navy); line-height: 1;
    display: flex; align-items: center; gap: 12px;
  }
  .brand-mark { width: 16px; height: 16px; background: var(--red); flex: none; }

  /* Back side */
  .card-back .brand-name {
    position: absolute; left: 0; right: 0; top: 110px;
    justify-content: center; font-size: 44px;
  }
  .divider {
    position: absolute; left: 0; right: 0; top: 250px;
    height: 1px; background: var(--red);
  }
  .badge-fair-housing {
    position: absolute; right: 26px; top: 196px; width: 44px; height: 40px;
  }
  .badge-realtor {
    position: absolute; left: 26px; bottom: 24px; width: 40px; height: 46px;
  }
  .website {
    position: absolute; left: 0; right: 0; top: 300px; text-align: center;
    font-size: 17px; letter-spacing: 6px; color: var(--grey);
  }

  /* Front side */
  .card-front .brand-name {
    position: absolute; left: 56px; top: 56px; font-size: 38px;
  }
  .accent-notch {
    position: absolute; left: 0; top: 178px; width: 30px; height: 22px;
  }
  .agent { position: absolute; left: 56px; top: 168px; }
  .agent-name { font-size: 26px; font-weight: 700; color: var(--navy); }
  .agent-title { font-size: 19px; color: var(--red); margin-top: 2px; }
  .contact {
    position: absolute; left: 56px; top: 254px;
    font-size: 18px; color: var(--grey); line-height: 1.3;
  }
  .contact-lines { margin-top: 14px; }
  .contact-label { font-weight: 700; color: var(--navy); margin-right: 4px; }
</style>
</head>
<body>
  <main class="sheet">
    <section class="card card-back" aria-label="Card back">
      <div class="brand-name"><span class="brand-mark"></span>Brightfield Realty Group</div>
      <svg class="badge-fair-housing" viewBox="0 0 44 40" role="img" aria-label="Fair housing badge">
        <rect x="0" y="0" width="44" height="40" fill="var(--dark)"/>
      </svg>
      <div class="divider"></div>
      <p class="website">www.tobiasmerrowkl.com</p>
      <svg class="badge-realtor" viewBox="0 0 40 46" role="img" aria-label="Realtor badge">
        <rect x="0" y="0" width="40" height="46" fill="var(--dark)"/>
      </svg>
    </section>

    <section class="card card-front" aria-label="Card front">
      <div class="brand-name"><span class="brand-mark"></span>Brightfield Realty Group</div>
      <svg class="accent-notch" viewBox="0 0 30 22" aria-hidden="true">
        <polygon points="0,0 30,11 0,22" fill="var(--red)"/>
      </svg>
      <div class="agent">
        <p class="agent-name">Tobias Merrow, PA</p>
        <p class="agent-title">Realtor</p>
      </div>
      <div class="contact">
        <p>482 Lakeview Crossing Dr.</p>
        <p>Maple Hollow, FL 32790</p>
        <div class="contact-lines">
          <p><span class="contact-label">P:</span>555.210.4800</p>
          <p><span class="contact-label">M:</span>555.384.1927</p>
          <p><span class="contact-label">E:</span>merrowhomes@mailbox.com</p>
        </div>
      </div>
    </section>
  </main>
</body>
</html>
```